Leadership training for women Business + Spirit

I need a flyer for a leadership training to hand out after I've been doing public speaking. I would also like to send it as a PDF. so maybe A4 is a good size. I will probably also need a brochure, with some more in depth information, but to start with I like to just give them something so they get inspired to contact me for more information. You can see more of my style on www.brightmeadow.se . Its a training that combines business with spirit, heart with intellect. We focus both on strict leadership skills such as Setting objectives aligned with strategy, assess performance and spiritual practices such as meditation, connecting with your unique essence. I like the deign to communicate business and professional together with warmth, life and joy. Colourful with style. Empowerment. The attached style guide does not have to be followed strictly but please use it in combination with my site www.brightmeadow.se I've the logo in many different sizes. I've added the smallest one below. Use any images that you think might fit, doesn't have to be from my website, it could be from your resources. I've added some other images here in the brief too, I have many more but can't attach all of it :-).
Target Market(s)
Women in leadership positions age 30 - 60
Industry/Entity Type
Leadership
Look and feel

```html
<!DOCTYPE html>
<html lang="en">
<head>
<meta charset="utf-8">
<title>Bright Meadow – Leadership for Women</title>
<link href="https://fonts.googleapis.com/css2?family=Lato:wght@300;400;700;900&display=swap" rel="stylesheet">
<style>
  :root {
    --tan: #aa9e82;
    --navy: #1c3550;
    --magenta: #b02a70;
    --magenta-deep: #8f1f5a;
    --orange: #f0981f;
    --orange-deep: #e98a14;
    --white: #ffffff;
  }
  html, body { margin: 0; padding: 0; overflow: hidden; }
  body { width: 950px; height: 1200px; background: var(--white); font-family: 'Lato', sans-serif; color: var(--white); }
  .flyer { position: relative; width: 950px; height: 1200px; overflow: hidden; }

  .feature-band {
    position: absolute; left: 0; top: 330px; width: 950px; height: 350px;
    background: radial-gradient(ellipse at 30% 40%, #c8357f 0%, var(--magenta) 45%, var(--magenta-deep) 100%);
  }
  .header-art { position: absolute; left: 0; top: 0; }

  .intro { position: absolute; left: 330px; top: 50px; width: 620px; text-align: center; }
  .intro-name { margin: 0 0 14px; font-size: 27px; font-weight: 900; }
  .intro-text { margin: 0 auto 16px; width: 575px; font-size: 14px; line-height: 1.2; font-weight: 400; }
  .intro-quote { margin: 0; font-size: 19px; font-weight: 700; }

  .brand { position: absolute; left: 150px; top: 390px; display: flex; align-items: center; gap: 28px; }
  .brand-mark { width: 130px; height: 130px; border: 2px solid var(--white); border-radius: 50%; box-sizing: border-box; }
  .brand-name { font-size: 66px; font-weight: 300; letter-spacing: -1px; color: var(--white); }

  .mission { position: absolute; left: 33px; top: 550px; width: 882px; height: 102px; border: 3px solid var(--white); box-sizing: border-box; text-align: center; }
  .mission-title { position: absolute; left: 50%; top: -20px; transform: translateX(-50%); margin: 0; padding: 0 16px; background: var(--magenta); font-size: 28px; font-weight: 700; white-space: nowrap; line-height: 1.2; }
  .mission-text { margin: 22px 22px 0; font-size: 14px; line-height: 1.22; font-weight: 700; }

  .pillars { position: absolute; left: 0; top: 680px; width: 950px; height: 440px;
    background: linear-gradient(180deg, var(--orange-deep) 0%, var(--orange) 50%, #f2a43a 100%); }
  .pillar { position: absolute; top: 0; width: 262px; text-align: center; }
  .pillar:nth-child(1) { left: 42px; }
  .pillar:nth-child(2) { left: 342px; }
  .pillar:nth-child(3) { left: 642px; }
  .pillar-photo { margin-top: 26px; height: 156px; border: 4px solid var(--white); box-shadow: 3px 3px 0 rgba(255,255,255,0.6); }
  .photo-office { background: linear-gradient(135deg, #d9d6d0 0%, #e8a7a0 45%, #6d6a66 100%); }
  .photo-leaf { background: radial-gradient(circle at 55% 45%, #d4567a 0%, #6a7a2a 40%, #1a2210 100%); }
  .photo-summit { background: linear-gradient(180deg, #e8c9a8 0%, #c89a7a 55%, #4a3028 100%); }
  .pillar-text { margin: 30px 6px 0; font-size: 13px; line-height: 1.25; font-weight: 700; }

  .contact-bar { position: absolute; left: 0; top: 1120px; width: 950px; height: 80px; background: var(--navy);
    display: flex; align-items: center; justify-content: center; font-size: 26px; font-weight: 900; }
</style>
</head>
<body>
<div class="flyer">
  <div class="feature-band"></div>

  <svg class="header-art" width="950" height="430" viewBox="0 0 950 430">
    <defs>
      <linearGradient id="portraitTone" x1="0" y1="0" x2="1" y2="0">
        <stop offset="0" stop-color="#5e3f34"/>
        <stop offset="0.45" stop-color="#4a3a36"/>
        <stop offset="0.8" stop-color="#8c8170"/>
        <stop offset="1" stop-color="#aa9e82"/>
      </linearGradient>
      <clipPath id="headerEdge">
        <path d="M0,0 H950 V345 C860,360 780,395 640,390 C500,385 420,345 300,345 C180,345 90,365 0,385 Z"/>
      </clipPath>
    </defs>
    <path fill="#1c3550" d="M0,0 H950 V355 C860,372 780,408 640,404 C500,398 420,368 300,370 C180,372 90,395 0,425 Z"/>
    <g clip-path="url(#headerEdge)">
      <rect x="0" y="0" width="950" height="430" fill="#aa9e82"/>
      <g role="img" aria-label="Portrait photo of the coach in a white knit scarf against a brick wall">
        <rect x="0" y="0" width="345" height="430" fill="url(#portraitTone)"/>
      </g>
    </g>
  </svg>

  <section class="intro">
    <h1 class="intro-name">Helena Berg Strand</h1>
    <p class="intro-text">I am a modern mystic and leadership developer who has trained several hundreds of leaders on eg. Nordvik Bank, Lysa Foods, Kronholm Brewing, Stegra Shoes, Tryggo Insurance, Vindkraft Nord, Netora. I have been on my spiritual journey since childhood, meditated since I was 16 and after a decade of extreme skiing and rock climbing I have weighted my adult professional life on the spiritual awakening and to coach people to a more living life.</p>
    <p class="intro-text">With BRIGHT MEADOW I offer opportunities for you as a woman to strengthen contact with your inner being and your own very holy wisdom. To unite the interior with the exterior and deepen your leadership, both as a private person and in your professional role. You are very welcome!</p>
    <p class="intro-quote">"I live as I learn, that's my strength."</p>
  </section>

  <div class="brand">
    <div class="brand-mark"></div>
    <div class="brand-name">Bright Meadow</div>
  </div>

  <section class="mission">
    <h2 class="mission-title">BRIGHT MEADOW</h2>
    <p class="mission-text">We have become good at performing at the expense of contact with our body and soul, when we really need the opposite. A holistic leadership of people who have good self-knowledge, who grow in the challenges, people who know that vulnerability gives an incomparable strength and does not underestimate their brilliant intellect. The world needs people who live and lead from a whole new place. The show feminine can lead us there.</p>
  </section>

  <section class="pillars">
    <article class="pillar">
      <div class="pillar-photo photo-office" role="img" aria-label="Photo of a smiling businesswoman on the phone at her desk"></div>
      <p class="pillar-text">As modern women, many of us share a basic pattern of just pushing through and biting, delivering and being good by driving over both body and soul. What if there is another way to get results? A way in which you combine practical skills in leadership such as goals, performance management and coaching with presence in both body, heart and soul. A way that lets soul, heart, achievement and business go hand in hand.</p>
    </article>
    <article class="pillar">
      <div class="pillar-photo photo-leaf" role="img" aria-label="Photo of a young pink plant sprouting from a log"></div>
      <p class="pillar-text">Before spirituality became its own concept and concept, before the word even emerged or religions and new age seized it, it already existed as a natural part of our lives. We are all valuable just by being, without performing. We are all in contact with something bigger, everything is connected and is part of the same being. Life is sacred. Remembering and living this is spirituality for me.</p>
    </article>
    <article class="pillar">
      <div class="pillar-photo photo-summit" role="img" aria-label="Photo of a woman with open arms on a mountain top above misty valleys"></div>
      <p class="pillar-text">We live in a culture that teaches us to shut down, keep the cover on our dreams and constantly put what is most important to us at the bottom of the list, while we are rushing towards a future that promises us all that we do not take time till now. Bright Meadow is a context that strengthens you, both as being and woman to wake up, grow and succeed with what you want to live before you die. It's empowerment!</p>
    </article>
  </section>

  <footer class="contact-bar">0700-55 01 23 | BRIGHTMEADOW.SE | Folj oss pa: our social pages</footer>
</div>
</body>
</html>
```